Brand Identity Stationary Package

Hello I'm looking for a full branding package for my Property Management Company. I have a logo but looking to have the following
Business Card
Email signature
Facebook cover photo
Letterhead (word.doc)
#10 Envelope
Pocket Folder - link to 9x12 pocket folder design specs https://www.printorbit-example.ca/marketing-materials/presentation-folders
would like everything to match and be brand identifiable. The company looks after residential properties/apartments and some commercial properties. Attached is a zip of the files.
For Business Card
Name: Gareth Lindqvist
Position: Operations Manager
Number: 1 (555) 384-2917
Email: Gareth@harborkey-example.ca
Website: Harborkey-example.ca
Property Management

```html
<!DOCTYPE html>
<html lang="en">
<head>
<meta charset="UTF-8">
<title>Harborkey Letterhead</title>
<link href="https://fonts.googleapis.com/css2?family=Montserrat:wght@400;500;700&display=swap" rel="stylesheet">
<style>
  :root {
    --backdrop: #ebebeb;
    --paper: #ffffff;
    --brand-green: #84ac3a;
    --brand-black: #111111;
    --text-dark: #222222;
  }
  * { margin: 0; padding: 0; box-sizing: border-box; }
  html, body {
    width: 1200px;
    height: 874px;
    overflow: hidden;
    background: var(--backdrop);
    font-family: "Montserrat", Arial, sans-serif;
  }
  .letterhead {
    position: absolute;
    left: 310px;
    top: 27px;
    width: 580px;
    height: 820px;
    background: var(--paper);
    box-shadow: 0 2px 10px rgba(0,0,0,0.08);
    overflow: hidden;
  }
  .brand-name {
    position: absolute;
    left: 40px;
    top: 62px;
    font-weight: 700;
    font-size: 26px;
    letter-spacing: 2px;
    color: var(--brand-black);
    line-height: 1;
  }
  .contact-block {
    position: absolute;
    left: 380px;
    top: 30px;
    padding-left: 12px;
    border-left: 1px solid var(--brand-green);
    color: var(--text-dark);
    font-size: 9.5px;
    line-height: 1.5;
    font-style: normal;
  }
  .contact-name {
    font-weight: 700;
    color: var(--brand-green);
    text-transform: uppercase;
    font-size: 10px;
  }
  .contact-role { font-weight: 500; margin-bottom: 2px; }
  .contact-line {
    display: flex;
    align-items: center;
    gap: 6px;
    white-space: nowrap;
  }
  .contact-icon { width: 9px; height: 9px; flex: none; }
  .footer-band {
    position: absolute;
    left: 0;
    bottom: 0;
    width: 580px;
    height: 120px;
  }
  .band-green { fill: var(--brand-green); }
  .band-rule { stroke: var(--brand-black); stroke-width: 3; }
  .icon-green { fill: var(--brand-green); }
</style>
</head>
<body>
  <main class="letterhead">
    <div class="brand-name">HARBORKEY</div>

    <address class="contact-block">
      <div class="contact-name">Gareth Lindqvist</div>
      <div class="contact-role">Operations Manager</div>
      <div class="contact-line">
        <svg class="contact-icon" viewBox="0 0 10 10"><path class="icon-green" d="M2 0.5 L3.6 0.5 L4.2 2.8 L3 3.6 C3.6 5 5 6.4 6.4 7 L7.2 5.8 L9.5 6.4 L9.5 8 C9.5 9 8.8 9.5 8 9.5 C3.8 9.5 0.5 6.2 0.5 2 C0.5 1.2 1 0.5 2 0.5 Z"/></svg>
        <span>1 (555) 384-2917</span>
      </div>
      <div class="contact-line">
        <svg class="contact-icon" viewBox="0 0 10 10"><path class="icon-green" d="M0.5 2 L9.5 2 L9.5 8.5 L0.5 8.5 Z M1.2 2.6 L5 5.6 L8.8 2.6 Z" fill-rule="evenodd"/></svg>
        <span>Gareth@harborkey-example.ca</span>
      </div>
      <div class="contact-line">
        <svg class="contact-icon" viewBox="0 0 10 10"><circle class="icon-green" cx="5" cy="5" r="4.5"/><path d="M0.8 5 H9.2 M5 0.6 C2.6 3 2.6 7 5 9.4 M5 0.6 C7.4 3 7.4 7 5 9.4" stroke="#fff" stroke-width="0.7" fill="none"/></svg>
        <span>Harborkey-example.ca</span>
      </div>
    </address>

    <svg class="footer-band" viewBox="0 0 580 120" aria-hidden="true">
      <line class="band-rule" x1="0" y1="84" x2="580" y2="84"/>
      <rect class="band-green" x="0" y="92" width="580" height="28"/>
    </svg>
  </main>
</body>
</html>
```